UI Improvement for FlorKeep app

We are looking for a talented UI/UX designer to REFINE and enhance the visual design of our mobile application, FlorKeep. The app is fully functional, but we need a designer to improve its aesthetics by specifying design elements such as fonts, colors, spacing, and component styles.
Your task will be to analyze the CURRENT UI and provide detailed design specifications that will make the app more visually appealing, modern, and user-friendly.
TODO:
Review the existing FlorKeep app design (see attachments) and identify areas for visual improvement.
Provide a detailed UI style guide, including:
Typography (font choices, sizes, and weights)
Color palette (primary, secondary, and accent colors)
Component styling (buttons, forms, icons, and interactive elements)
Spacing and layout guidelines (margins, paddings, and alignment)
Ensure the design remains clean, modern, and professional while maintaining usability and accessibility.
Provide design mockups or visual examples (if possible) to illustrate the proposed changes.
Deliverables:
A UI Style Guide (PDF or Figma file) with specifications on fonts, colors, spacing, and UI components.
Optionally, before/after mockups or examples demonstrating the improvements.
Ideal Designer:
Strong experience in mobile UI/UX design.
Understanding of modern design trends and best practices.
Ability to communicate design choices clearly for easy developer implementation.
I have attached 7 images showcasing the main UI screens used in the FlorKeep app. These screens need visual enhancements to improve their overall look and user experience.
The images represent the current design in three key modes:
LIST Mode – Displays data in a structured list format.
READ Mode – Shows detailed information when a user selects an item.
ADD/EDIT Mode – Allows users to input or modify information.
Additionally, there is a ‘MORE’ page, which serves as a menu listing other features of the application.
Task Objective:
Please refine and improve these UIs to create a more modern, visually appealing, and user-friendly experience. Focus on typography, colors, spacing, and component styling to ensure a cohesive and polished design.
Look and feel
Each slider illustrates characteristics of the customer's brand and the style your logo design should communicate.

```html
<!DOCTYPE html>
<html lang="en">
<head>
<meta charset="utf-8">
<title>FlorKeep – Pilot screens</title>
<link rel="stylesheet" href="https://fonts.googleapis.com/css2?family=Montserrat:wght@700&family=Roboto:wght@400;500;700&display=swap">
<style>
:root{
  --canvas:#959597;
  --screen:#e9f1f8;
  --panel:#ffffff;
  --row:#e4f1fa;
  --row-note:#f8f8e8;
  --blue-deep:#0a4fa6;
  --blue-mid:#0277c6;
  --blue-bright:#0796dc;
  --ink:#1f1f1f;
  --ink-soft:#3a3a3a;
  --muted:#7b7b7b;
  --line:#bfc7cf;
}
*{box-sizing:border-box;margin:0;padding:0}
html,body{width:1200px;height:1120px;overflow:hidden;background:var(--canvas)}
body{font-family:"Roboto",Arial,sans-serif;color:var(--ink)}
.stage{position:absolute;left:0;top:0;width:1570px;height:1465px;transform:scale(.76433);transform-origin:0 0}
.phone{position:absolute;top:100px;width:414px;height:1265px;background:var(--screen);overflow:hidden}
.phone--list{left:131px}.phone--contact{left:578px}.phone--detail{left:1025px}

.app-bar{position:absolute;left:0;top:0;width:414px;height:58px;border-radius:0 0 46px 46px;
  background:linear-gradient(90deg,var(--blue-deep) 0%,var(--blue-mid) 60%,var(--blue-bright) 100%);
  display:flex;align-items:center;justify-content:center}
.brand{font-family:"Montserrat",Arial,sans-serif;font-weight:700;font-size:30px;color:#fff;letter-spacing:.5px}

.title-row{position:absolute;left:0;top:78px;width:414px;height:40px}
.title{position:absolute;left:0;right:0;text-align:center;font-size:26px;font-weight:700;line-height:40px;color:var(--ink)}
.back{position:absolute;left:27px;top:7px;width:26px;height:26px}
.round-btn{position:absolute;top:5px;width:30px;height:30px;border-radius:50%;display:flex;align-items:center;justify-content:center}
.round-btn--add{left:309px;background:var(--blue-bright)}
.round-btn--more{left:347px;background:var(--blue-deep)}

.search{position:absolute;left:26px;top:133px;width:363px;height:52px;border:1.5px solid var(--line);border-radius:26px;background:#fff;
  font-size:15px;color:var(--ink-soft);padding-left:28px;line-height:49px}
.search-go{position:absolute;right:4px;top:5px;width:38px;height:38px;border-radius:50%;background:var(--blue-deep);display:flex;align-items:center;justify-content:center}

.panel{position:absolute;left:19px;width:377px;background:var(--panel);border:1.5px solid var(--line);border-radius:20px}
.phone--list .panel,.phone--contact .panel{top:210px;height:862px}
.phone--detail .panel{top:195px;height:914px}

.pilot-item{position:absolute;left:19px;width:338px;height:93px;background:var(--row);border-radius:5px}
.avatar{position:absolute;left:30px;top:8px;width:76px;height:76px;border-radius:50%}
.av-a{background:radial-gradient(circle at 50% 38%,#c9a58a 0 22%,#3d4652 60%,#8aa0b5 100%)}
.av-b{background:radial-gradient(circle at 50% 38%,#b88b6c 0 22%,#d9d3c8 60%,#6b5d52 100%)}
.av-c{background:radial-gradient(circle at 50% 38%,#e2b79a 0 22%,#f1f3f5 60%,#9aa5ad 100%)}
.av-d{background:radial-gradient(circle at 50% 38%,#6d4632 0 22%,#f2f0ec 60%,#c5a789 100%)}
.pilot-name{position:absolute;left:134px;top:20px;font-size:20px;font-weight:500;color:var(--ink)}
.pilot-meta{position:absolute;left:134px;top:52px;font-size:15px;color:var(--ink-soft)}

.add-row{position:absolute;left:19px;width:338px;height:57px;background:var(--row);border-radius:5px;display:flex;align-items:center}
.add-row .plus{margin-left:34px;width:30px;height:30px;border-radius:50%;background:var(--blue-bright);display:flex;align-items:center;justify-content:center;flex:none}
.add-row .label{margin-left:28px;font-size:17px;color:var(--ink)}

.summary{position:absolute;left:19px;width:338px;background:var(--row);border-radius:5px}
.summary--note{background:var(--row-note)}
.summary h3{position:absolute;left:33px;font-size:16px;font-weight:500;color:var(--ink)}
.summary .collapse{position:absolute;right:-10px;top:22px;font-size:14px;color:var(--muted)}
.summary p{position:absolute;left:33px;font-size:14px;line-height:21px;color:var(--ink-soft)}
.expand{position:absolute;width:20px;height:20px}

.detail-block{position:absolute;left:19px;width:338px;background:var(--row);border-radius:5px}
.field-label{position:absolute;left:33px;font-size:16px;font-weight:700;color:var(--ink)}
.field-value{position:absolute;left:33px;font-size:18px;color:var(--ink-soft)}
.dots-btn{position:absolute;width:30px;height:30px;border-radius:50%;background:var(--blue-deep);display:flex;align-items:center;justify-content:center}
.airport{position:absolute;left:33px;font-size:16px;font-weight:500;line-height:28px;color:var(--ink)}

.tab-bar{position:absolute;left:0;top:1116px;width:414px;height:149px;border-radius:52px 52px 0 0;
  background:linear-gradient(100deg,var(--blue-deep) 0%,var(--blue-mid) 55%,var(--blue-bright) 100%)}
.tab{position:absolute;top:36px;width:90px;margin-left:-45px;text-align:center;color:#fff;font-size:16px;line-height:20px}
.tab-icon{width:44px;height:44px;border-radius:50%;background:rgba(255,255,255,.32);margin:0 auto 14px;display:flex;align-items:center;justify-content:center}
.tab--active .tab-icon{background:#fff}
.t1{left:50px}.t2{left:128px}.t3{left:207px}.t4{left:285px}.t5{left:362px}
</style>
</head>
<body>
<svg width="0" height="0" style="position:absolute">
  <defs>
    <symbol id="i-plus" viewBox="0 0 12 12"><path d="M6 1v10M1 6h10" stroke="#fff" stroke-width="2" stroke-linecap="round"/></symbol>
    <symbol id="i-dots" viewBox="0 0 14 4"><circle cx="2" cy="2" r="1.6" fill="#fff"/><circle cx="7" cy="2" r="1.6" fill="#fff"/><circle cx="12" cy="2" r="1.6" fill="#fff"/></symbol>
    <symbol id="i-search" viewBox="0 0 16 16"><circle cx="6.5" cy="6.5" r="4.5" fill="none" stroke="#fff" stroke-width="2.2"/><path d="M10 10l4 4" stroke="#fff" stroke-width="2.4" stroke-linecap="round"/></symbol>
    <symbol id="i-back" viewBox="0 0 26 26"><circle cx="13" cy="13" r="11.5" fill="none" stroke="#222" stroke-width="1.6"/><path d="M18 13H8.5M12.5 9l-4 4 4 4" fill="none" stroke="#222" stroke-width="1.6" stroke-linecap="round" stroke-linejoin="round"/></symbol>
    <symbol id="i-down" viewBox="0 0 20 20"><circle cx="10" cy="10" r="8.6" fill="none" stroke="#333" stroke-width="1.4"/><path d="M10 5.5v8M6.8 10.5l3.2 3.2 3.2-3.2" fill="none" stroke="#333" stroke-width="1.4" stroke-linecap="round" stroke-linejoin="round"/></symbol>
    <symbol id="i-person" viewBox="0 0 20 20"><circle cx="10" cy="6.5" r="4"/><path d="M2.5 18c0-4.2 3.4-6.5 7.5-6.5s7.5 2.3 7.5 6.5z"/></symbol>
    <symbol id="i-pilot" viewBox="0 0 20 20"><path d="M4 4.5l6-2.5 6 2.5v1.8H4z"/><circle cx="10" cy="9" r="3.2"/><path d="M3 19c0-4 3-6.2 7-6.2s7 2.2 7 6.2z"/></symbol>
    <symbol id="i-plane" viewBox="0 0 20 20"><path d="M19 10c0-.8-.7-1.3-1.5-1.3h-4.7L8.6 2H6.8l2.3 6.7H4.6L3 6.6H1.6l1 3.4-1 3.4H3l1.6-2.1h4.5L6.8 18h1.8l4.2-6.7h4.7c.8 0 1.5-.5 1.5-1.3z"/></symbol>
    <symbol id="i-hands" viewBox="0 0 22 20"><path d="M2 5c1 0 1.6.8 1.8 2l.7 4.2 2.8 2.3c.9.8 1.5 1.6 1.5 2.8V19H5.5l-3.2-4C1.7 14.3 1 12.6 1 11V6c0-.6.4-1 1-1zM20 5c-1 0-1.6.8-1.8 2l-.7 4.2-2.8 2.3c-.9.8-1.5 1.6-1.5 2.8V19h3.3l3.2-4c.6-.7 1.3-2.4 1.3-4V6c0-.6-.4-1-1-1z"/><path d="M11 3.5c1-1.3 3.2-.8 3 1-.2 1.4-3 3.3-3 3.3S8.2 5.9 8 4.5c-.2-1.8 2-2.3 3-1z"/></symbol>
  </defs>
</svg>

<div class="stage">

  <!-- List mode -->
  <section class="phone phone--list">
    <header class="app-bar"><span class="brand">FlorKeep</span></header>
    <div class="title-row">
      <h1 class="title">Pilots</h1>
      <span class="round-btn round-btn--add"><svg width="12" height="12"><use href="#i-plus"/></svg></span>
      <span class="round-btn round-btn--more"><svg width="14" height="4"><use href="#i-dots"/></svg></span>
    </div>
    <div class="search">Advanced Search<span class="search-go"><svg width="16" height="16"><use href="#i-search"/></svg></span></div>
    <div class="panel">
      <div class="pilot-item" style="top:19px"><div class="avatar av-a" role="img" aria-label="Pilot portrait photo"></div><div class="pilot-name">Harlow,Dean,Miles,</div><div class="pilot-meta">3182133,9/30/24</div></div>
      <div class="pilot-item" style="top:121px"><div class="avatar av-b" role="img" aria-label="Pilot portrait photo"></div><div class="pilot-name">Corwin,Peter</div><div class="pilot-meta">3182133,9/30/24</div></div>
      <div class="pilot-item" style="top:222px"><div class="avatar av-c" role="img" aria-label="Pilot portrait photo"></div><div class="pilot-name">Renzo,Mia,Clara</div><div class="pilot-meta">3182133,9/30/24</div></div>
      <div class="pilot-item" style="top:324px"><div class="avatar av-c" role="img" aria-label="Pilot portrait photo"></div><div class="pilot-name">Tobin Arvelo</div><div class="pilot-meta">3182133,9/30/24</div></div>
      <div class="pilot-item" style="top:426px"><div class="avatar av-a" role="img" aria-label="Pilot portrait photo"></div><div class="pilot-name">Harlow,Dean,Miles,</div><div class="pilot-meta">3182133,9/30/24</div></div>
      <div class="pilot-item" style="top:528px"><div class="avatar av-d" role="img" aria-label="Pilot portrait photo"></div><div class="pilot-name">Corwin,Peter</div><div class="pilot-meta">3182133,9/30/24</div></div>
      <div class="pilot-item" style="top:629px"><div class="avatar av-b" role="img" aria-label="Pilot portrait photo"></div><div class="pilot-name">Renzo,Mia,Clara</div><div class="pilot-meta">3182133,9/30/24</div></div>
      <div class="pilot-item" style="top:731px"><div class="avatar av-a" role="img" aria-label="Pilot portrait photo"></div><div class="pilot-name">Tobin Arvelo</div><div class="pilot-meta">3182133,9/30/24</div></div>
    </div>
    <nav class="tab-bar">
      <div class="tab t1"><div class="tab-icon"><svg width="20" height="20" fill="#fff"><use href="#i-person"/></svg></div>Contact</div>
      <div class="tab t2 tab--active"><div class="tab-icon"><svg width="20" height="20" fill="#0a4fa6"><use href="#i-pilot"/></svg></div>Pilot</div>
      <div class="tab t3"><div class="tab-icon"><svg width="20" height="20" fill="#fff"><use href="#i-plane"/></svg></div>Plane</div>
      <div class="tab t4"><div class="tab-icon"><svg width="22" height="20" fill="#fff"><use href="#i-hands"/></svg></div>Flt<br>Request</div>
      <div class="tab t5"><div class="tab-icon"><svg width="14" height="4"><use href="#i-dots"/></svg></div>More</div>
    </nav>
  </section>

  <!-- Add / edit mode -->
  <section class="phone phone--contact">
    <header class="app-bar"><span class="brand">FlorKeep</span></header>
    <div class="title-row">
      <svg class="back"><use href="#i-back"/></svg>
      <h1 class="title">Contact</h1>
      <span class="round-btn round-btn--add"><svg width="12" height="12"><use href="#i-plus"/></svg></span>
      <span class="round-btn round-btn--more"><svg width="14" height="4"><use href="#i-dots"/></svg></span>
    </div>
    <div class="search">Advanced Search<span class="search-go"><svg width="16" height="16"><use href="#i-search"/></svg></span></div>
    <div class="panel">
      <div class="add-row" style="top:18px"><span class="plus"><svg width="12" height="12"><use href="#i-plus"/></svg></span><span class="label">Add Email -e</span></div>
      <div class="add-row" style="top:81px"><span class="plus"><svg width="12" height="12"><use href="#i-plus"/></svg></span><span class="label">Add Social Media -e</span></div>
      <div class="add-row" style="top:145px"><span class="plus"><svg width="12" height="12"><use href="#i-plus"/></svg></span><span class="label">Add Emergency Contact -e</span></div>
      <div class="add-row" style="top:208px"><span class="plus"><svg width="12" height="12"><use href="#i-plus"/></svg></span><span class="label">Add Personal Information -e</span></div>
      <div class="add-row" style="top:271px"><span class="plus"><svg width="12" height="12"><use href="#i-plus"/></svg></span><span class="label">Add Work Info -e</span></div>
      <div class="add-row" style="top:334px"><span class="plus"><svg width="12" height="12"><use href="#i-plus"/></svg></span><span class="label">Add Skills/Talents -e</span></div>
      <div class="add-row" style="top:398px"><span class="plus"><svg width="12" height="12"><use href="#i-plus"/></svg></span><span class="label">Add Resources -e</span></div>
      <div class="summary summary--note" style="top:461px;height:93px">
        <h3 style="top:22px">Pilots-e</h3><span class="collapse">Collapse</span>
        <p style="top:52px">Bramley,Owen,3647946,0/31/23</p>
        <svg class="expand" style="left:289px;top:60px"><use href="#i-down"/></svg>
      </div>
      <div class="summary" style="top:561px;height:134px">
        <h3 style="top:22px">Aircraft Owner-e</h3><span class="collapse">Collapse</span>
        <p style="top:51px">Personal:Bramley,Owen:Skyvane:<br>18T Skyvane Aircraft Company<br>Single Engine,1100</p>
        <svg class="expand" style="left:289px;top:60px"><use href="#i-down"/></svg>
      </div>
      <div class="summary" style="top:702px;height:134px">
        <h3 style="top:22px">Aircraft Owner-e</h3><span class="collapse">Collapse</span>
        <p style="top:51px">Personal:Bramley,Owen:Skyvane:<br>18T Skyvane Aircraft Company<br>Single Engine,1100</p>
        <svg class="expand" style="left:289px;top:60px"><use href="#i-down"/></svg>
      </div>
    </div>
    <nav class="tab-bar">
      <div class="tab t1 tab--active"><div class="tab-icon"><svg width="20" height="20" fill="#0a4fa6"><use href="#i-person"/></svg></div>Contact</div>
      <div class="tab t2"><div class="tab-icon"><svg width="20" height="20" fill="#fff"><use href="#i-pilot"/></svg></div>Pilot</div>
      <div class="tab t3"><div class="tab-icon"><svg width="20" height="20" fill="#fff"><use href="#i-plane"/></svg></div>Plane</div>
      <div class="tab t4"><div class="tab-icon"><svg width="22" height="20" fill="#fff"><use href="#i-hands"/></svg></div>Flt<br>Request</div>
      <div class="tab t5"><div class="tab-icon"><svg width="14" height="4"><use href="#i-dots"/></svg></div>More</div>
    </nav>
  </section>

  <!-- Read mode -->
  <section class="phone phone--detail">
    <header class="app-bar"><span class="brand">FlorKeep</span></header>
    <div class="title-row">
      <svg class="back"><use href="#i-back"/></svg>
      <h1 class="title">Pilot</h1>
      <span class="round-btn round-btn--add"><svg width="12" height="12"><use href="#i-plus"/></svg></span>
      <span class="round-btn round-btn--more"><svg width="14" height="4"><use href="#i-dots"/></svg></span>
    </div>
    <div class="search">Advanced Search<span class="search-go"><svg width="16" height="16"><use href="#i-search"/></svg></span></div>
    <div class="panel">
      <div class="detail-block" style="top:17px;height:427px">
        <div class="add-row" style="left:0;top:0;background:transparent"><span class="plus"><svg width="12" height="12"><use href="#i-plus"/></svg></span><span class="label">Add Email -e</span></div>
        <span class="dots-btn" style="left:288px;top:15px"><svg width="14" height="4"><use href="#i-dots"/></svg></span>
        <div class="field-label" style="top:74px">Pilots-e</div>
        <div class="field-value" style="top:102px">Harlow,Dean,Miles</div>
        <div class="field-label" style="top:143px">Pilot Certificate No-e</div>
        <div class="field-value" style="top:171px">3647946</div>
        <div class="field-label" style="top:209px">Medical Expiration Date-e</div>
        <div class="field-value" style="top:237px">09/30/24</div>
        <div class="field-label" style="top:277px">Flight Review Expiration Date-e</div>
        <div class="field-value" style="top:305px">06/30/24</div>
        <div class="field-label" style="top:349px">Total Flight Time-e</div>
        <div class="field-value" style="top:377px">2500</div>
      </div>
      <div class="detail-block" style="top:450px;height:94px">
        <div class="airport" style="top:17px">X 35,Pine Cove Airport,<br>Pine City,FL,32625 11,2500</div>
        <svg class="expand" style="left:289px;top:23px"><use href="#i-down"/></svg>
      </div>
      <div class="detail-block" style="top:550px;height:94px">
        <div class="airport" style="top:17px">C 35,Ridgeway Municipal Airport,<br>Ridgeway,CO.FL,4,800 ft</div>
        <svg class="expand" style="left:289px;top:23px"><use href="#i-down"/></svg>
      </div>
      <div class="add-row" style="top:652px"><span class="plus"><svg width="12" height="12"><use href="#i-plus"/></svg></span><span class="label">Add Base Airport -e</span></div>
      <div class="add-row" style="top:715px"><span class="plus"><svg width="12" height="12"><use href="#i-plus"/></svg></span><span class="label">Add Ratings -e</span></div>
      <div class="detail-block" style="top:779px;height:125px">
        <div class="field-label" style="top:11px">Contact-e</div>
        <div class="field-value" style="top:36px">Harlow,Dean,Miles</div>
        <span class="dots-btn" style="left:288px;top:16px"><svg width="14" height="4"><use href="#i-dots"/></svg></span>
        <div class="field-label" style="top:67px">Phone -e</div>
        <div class="field-value" style="top:93px">555-014-2793</div>
      </div>
    </div>
    <nav class="tab-bar">
      <div class="tab t1"><div class="tab-icon"><svg width="20" height="20" fill="#fff"><use href="#i-person"/></svg></div>Contact</div>
      <div class="tab t2 tab--active"><div class="tab-icon"><svg width="20" height="20" fill="#0a4fa6"><use href="#i-pilot"/></svg></div>Pilot</div>
      <div class="tab t3"><div class="tab-icon"><svg width="20" height="20" fill="#fff"><use href="#i-plane"/></svg></div>Plane</div>
      <div class="tab t4"><div class="tab-icon"><svg width="22" height="20" fill="#fff"><use href="#i-hands"/></svg></div>Flt<br>Request</div>
      <div class="tab t5"><div class="tab-icon"><svg width="14" height="4"><use href="#i-dots"/></svg></div>More</div>
    </nav>
  </section>

</div>
</body>
</html>
```